Kellwyn Surface Records

I have a current web site that it looking quite aged and it needs a new lease of life. This is a Graffiti Management Website so is all about data processing and management of information. I want a html 5 view on any platform design. clean crisp and new. I have provided some screen shots of my current site.

Target Market(s)

The Target Market will be local government. most users will not be heavy pc users

Industry/Entity Type

Management

Font styles to use
Sans Serif
Other font styles liked:
• web font like calibri

Colors

Designer to choose colors to be used in the design.

Requirements
Must have
• Must have menus similar to attachments

```html
<!DOCTYPE html>
<html lang="en">
<head>
<meta charset="utf-8">
<title>Kellwyn Surface Records</title>
<link rel="stylesheet" href="https://fonts.googleapis.com/css2?family=Roboto:wght@300;400;500;700&display=swap">
<style>
:root{
  --accent:#f1566a;
  --accent-dark:#d9435a;
  --ink:#1f1f21;
  --text:#333336;
  --muted:#666a70;
  --rule:#c9c9cc;
  --white:#ffffff;
  --dark:#333336;
  --darker:#2e2e30;
  --footer:#3a3a3e;
  --panel-bar:#dcdcde;
}
*{box-sizing:border-box;margin:0;padding:0}
html,body{width:1200px;height:2712px;overflow:hidden}
body{font-family:"Roboto",Arial,sans-serif;color:var(--text);background:var(--white);position:relative}
.abs{position:absolute}

/* header */
.site-header{position:absolute;left:0;top:0;width:1200px;height:136px;background:var(--white)}
.brand{position:absolute;left:0;width:1200px;top:36px;text-align:center;font-size:34px;font-weight:700;letter-spacing:2px;color:var(--ink);text-transform:uppercase}
.account{position:absolute;top:50px;right:18px;display:flex;gap:11px}
.account a{display:block;height:40px;line-height:38px;border:2px solid var(--ink);padding:0 14px;font-size:15px;font-weight:700;color:var(--ink);text-decoration:none;text-transform:uppercase}

/* nav */
.main-nav{position:absolute;left:0;top:136px;width:1200px;height:68px;background:var(--accent)}
.main-nav a{position:absolute;top:0;height:68px;line-height:64px;transform:translateX(-50%);color:var(--white);font-weight:700;font-size:19px;text-decoration:none;text-transform:uppercase;white-space:nowrap}
.main-nav a.current::after{content:"";position:absolute;left:-12px;right:-12px;bottom:10px;height:4px;background:#8a3a44}

/* hero */
.hero{position:absolute;left:0;top:204px;width:1200px;height:591px;background:radial-gradient(ellipse at 40% 45%,#5e5e62 0%,#3b3b3f 55%,#262629 100%)}
.hero h1{position:absolute;left:82px;top:166px;font-weight:300;font-size:48px;line-height:58px;color:var(--white);text-transform:uppercase}
.hero p{position:absolute;left:82px;top:300px;width:560px;font-size:18px;line-height:24px;color:#e6e6e8}
.btn{display:block;background:var(--accent);color:var(--white);text-decoration:none;text-transform:uppercase;text-align:center}
.hero .btn{position:absolute;left:83px;top:388px;width:182px;height:56px;line-height:56px;font-size:18px}
.hero-photo{position:absolute;left:656px;top:140px;width:512px;height:302px;border:7px solid var(--white);background:linear-gradient(160deg,#b9a48e 0%,#8a6c57 40%,#4f6f8f 70%,#6b6a6e 100%);transform:rotate(-1deg)}
.thumb{position:absolute;width:98px;height:98px;border-radius:50%;border:6px solid var(--white)}
.dots{position:absolute;left:1060px;top:508px;display:flex;gap:4px}
.dots span{width:11px;height:11px;border-radius:50%;background:#8a8a8e}
.dots span.on{background:var(--accent)}

/* section basics */
.section-title{position:absolute;font-size:30px;font-weight:400;text-transform:uppercase}
.more-row{position:absolute;left:79px;width:1042px;height:44px}
.more-row::before{content:"";position:absolute;left:0;right:0;top:21px;height:2px;background:#9a9aa0}
.more-row .btn{position:absolute;left:441px;top:0;width:126px;height:44px;line-height:44px;font-size:15px;text-transform:none}

/* products */
.products{position:absolute;left:0;top:795px;width:1200px;height:550px}
.product{position:absolute;top:130px;width:230px;text-align:center}
.product h3{font-size:18px;font-weight:700;text-transform:uppercase;color:var(--ink);padding-bottom:14px;border-bottom:1px solid var(--rule)}
.product svg{display:block;margin:26px auto 0}
.product p{margin-top:24px;font-size:14px;line-height:20px;color:var(--text);padding:0 30px}

/* about / report */
.info{position:absolute;left:0;top:1345px;width:1200px;height:508px;background:var(--dark);color:var(--white)}
.info .divider{position:absolute;left:553px;top:25px;width:1px;height:450px;background:#55555a}
.info h2{position:absolute;top:40px;font-size:30px;font-weight:400;text-transform:uppercase;padding-bottom:10px;border-bottom:1px solid #55555a;width:430px}
.about-list{position:absolute;left:88px;top:120px;width:440px;list-style:none}
.about-list li{font-size:13px;line-height:17px;margin-bottom:20px}
.more-link{position:absolute;top:430px;font-size:13px;display:flex;align-items:center;gap:14px}
.more-link i{display:block;width:22px;height:22px;border-radius:50%;background:var(--accent)}
.report-intro{position:absolute;left:604px;top:120px;width:450px;font-size:13px;line-height:17px}
.report-panel{position:absolute;left:598px;top:200px;width:468px;height:200px;background:var(--white);border:4px solid #bdbdc1;padding:16px 10px 0 8px;color:var(--ink)}
.report-row{position:relative;height:56px}
.report-row .label{position:absolute;left:0;top:12px;font-size:13px}
.report-row .bar{position:absolute;left:0;top:36px;width:270px;height:5px;background:var(--panel-bar)}
.report-row .bar b{display:block;height:100%;background:var(--accent)}
.report-row .value{position:absolute;left:298px;top:0;font-size:34px;font-weight:400}
.report-row .delta{position:absolute;left:392px;top:10px;font-size:10px;color:#9a9aa0}
.report-row .delta::before{content:"";position:absolute;left:2px;top:-8px;border:4px solid transparent;border-top-color:var(--accent)}
.report-row .track{position:absolute;left:298px;top:43px;width:152px;height:4px;background:var(--panel-bar)}

/* benefits */
.benefits{position:absolute;left:0;top:1853px;width:1200px;height:520px}
.benefit{position:absolute;top:125px;width:244px;text-align:center}
.benefit .photo{height:136px}
.benefit h3{margin-top:20px;font-size:15px;font-weight:400;text-transform:uppercase;color:var(--ink);padding-bottom:10px;border-bottom:1px solid var(--rule)}
.benefit p{margin-top:14px;font-size:13px;line-height:19px;padding:0 12px}

/* help */
.help{position:absolute;left:0;top:2373px;width:1200px;height:181px;background:var(--darker);color:var(--white)}
.help h2{position:absolute;left:80px;top:24px;font-size:28px;font-weight:700;text-transform:uppercase}
.contact{position:absolute;top:100px;display:flex;align-items:center;gap:18px;font-size:15px;line-height:20px}
.contact.phone{font-size:26px}

/* footer */
.site-footer{position:absolute;left:0;top:2554px;width:1200px;height:158px;background:var(--footer)}
.footer-brand{position:absolute;left:40px;top:48px;font-size:34px;font-weight:700;letter-spacing:2px;color:#2a2a2d;text-transform:uppercase}
.copyright{position:absolute;left:86px;top:118px;font-size:12px;color:#d8d8da}
.social{position:absolute;right:54px;top:44px;display:flex;gap:8px}
.social span{width:30px;height:30px;border-radius:50%;border:2px solid #d8d8da}
</style>
</head>
<body>

<header class="site-header">
  <div class="brand">Kellwyn Surface Records</div>
  <nav class="account">
    <a href="#">Login</a>
    <a href="#">Demo Login</a>
  </nav>
</header>

<nav class="main-nav">
  <a class="current" href="#" style="left:163px">Home</a>
  <a href="#" style="left:339px">Products</a>
  <a href="#" style="left:533px">Reports</a>
  <a href="#" style="left:710px">Benefits</a>
  <a href="#" style="left:866px">Legislation</a>
  <a href="#" style="left:1040px">Contact Us</a>
</nav>

<section class="hero" role="img" aria-label="Blurred background photo of a graffiti covered wall">
  <h1>Helping you clean up<br>your community</h1>
  <p>KSR is an Online Database System to Manage Graffiti in your area or Your Properties</p>
  <a class="btn" href="#">Read More</a>
  <div class="hero-photo" role="img" aria-label="Photo of a brick building wall covered in colourful graffiti"></div>
  <div class="thumb" role="img" aria-label="Close-up graffiti detail" style="left:862px;top:112px;background:#8f7a6e"></div>
  <div class="thumb" role="img" aria-label="Close-up graffiti detail" style="left:954px;top:102px;background:#7a6a73"></div>
  <div class="thumb" role="img" aria-label="Close-up graffiti detail" style="left:1062px;top:102px;background:#a0766a"></div>
  <div class="dots"><span class="on"></span><span></span><span></span></div>
</section>

<section class="products">
  <h2 class="section-title" style="left:90px;top:40px;color:var(--ink)">Products</h2>

  <div class="product" style="left:40px">
    <h3>Graffiti Register</h3>
    <svg width="134" height="134" viewBox="0 0 134 134"><rect x="22" y="22" width="90" height="90" rx="8" transform="rotate(45 67 67)" fill="#111"/><rect x="58" y="60" width="18" height="32" rx="3" fill="#fff"/><rect x="62" y="52" width="10" height="7" fill="#fff"/><circle cx="52" cy="48" r="2" fill="#fff"/><circle cx="48" cy="54" r="2" fill="#fff"/><circle cx="54" cy="56" r="2" fill="#fff"/></svg>
    <p>KSR provides a National Register of Vandalism and Graffiti....</p>
  </div>

  <div class="product" style="left:314px">
    <h3>Graffiti Photos</h3>
    <svg width="134" height="134" viewBox="0 0 134 134"><rect x="22" y="22" width="90" height="90" rx="8" transform="rotate(45 67 67)" fill="#111"/><rect x="47" y="53" width="40" height="30" fill="none" stroke="#fff" stroke-width="3"/><path d="M50 80 L62 66 L70 74 L76 68 L84 80 Z" fill="#fff"/><circle cx="77" cy="61" r="3" fill="#fff"/></svg>
    <p>KSR allows its subscri -bers to add Digital Photogr aphs to the Graffiti Jobs...</p>
  </div>

  <div class="product" style="left:595px">
    <h3>Graffiti Archive</h3>
    <svg width="134" height="134" viewBox="0 0 134 134"><rect x="22" y="22" width="90" height="90" rx="8" transform="rotate(45 67 67)" fill="#111"/><path d="M53 46 H74 L82 54 V88 H53 Z" fill="none" stroke="#fff" stroke-width="3"/><rect x="65" y="58" width="5" height="18" rx="2" fill="#fff"/><circle cx="67.5" cy="79" r="4" fill="#fff"/></svg>
    <p>KSR will hold secure the commercial and sensitive details of your Graffit...</p>
  </div>

  <div class="product" style="left:878px">
    <h3>Searchable Database</h3>
    <svg width="134" height="134" viewBox="0 0 134 134"><rect x="22" y="22" width="90" height="90" rx="8" transform="rotate(45 67 67)" fill="#111"/><path d="M46 52 H60 L64 56 H86 V84 H46 Z" fill="none" stroke="#fff" stroke-width="3"/><circle cx="70" cy="70" r="7" fill="none" stroke="#fff" stroke-width="3"/><path d="M75 75 L82 82" stroke="#fff" stroke-width="3"/></svg>
    <p>KSR allows you to search your own records and limited data from others....</p>
  </div>

  <div class="more-row" style="top:443px"><a class="btn" href="#">More</a></div>
</section>

<section class="info">
  <div class="divider"></div>
  <h2 style="left:88px">About Us</h2>
  <ul class="about-list">
    <li>KSR is an Online Database System to Manage Graffiti in your area or Your Properties</li>
    <li>KSR allows you to Register, Track, Report and Archive Graffiti Jobs with Photographic Records.</li>
    <li>KSR records both Estimated and Actual hours and costs for each job, enabling you to track the effectiveness of Anti Graffiti policy.</li>
    <li>KSR allows sharing of Critical Graffiti Tag and Photographic Data between its subscribers, assisting with tracking down Serial Graffiti Offenders</li>
    <li>KSR has a Statistical and Comparison Reporting Systems to allow its subscribers to graphically report and compare their Graffiti Data.</li>
  </ul>
  <div class="more-link" style="left:88px">More <i></i></div>

  <h2 style="left:604px">Report</h2>
  <p class="report-intro">Statistical Reports can be done instantaneously and can be run on any data stored with in KSR. Charts and Graphs are available to clearly show trends and details for Management Purposes.</p>
  <div class="report-panel">
    <div class="report-row"><span class="label">Graffiti type Report (10 -10-2014 to 10-12-2014)</span><span class="bar"><b style="width:50%"></b></span><span class="value">50,5%</span><span class="delta">+23%</span><span class="track"></span></div>
    <div class="report-row"><span class="label">Graffiti type Report (10 -10-2014 to 10-12-2014)</span><span class="bar"><b style="width:20%"></b></span><span class="value">20%</span><span class="delta">-6%</span><span class="track"></span></div>
    <div class="report-row"><span class="label">Graffiti type Report (10 -10-2014 to 10-12-2014)</span><span class="bar"><b style="width:30%"></b></span><span class="value">29.5%</span><span class="delta">+9.7%</span><span class="track"></span></div>
  </div>
  <div class="more-link" style="left:604px">More <i></i></div>
</section>

<section class="benefits">
  <h2 class="section-title" style="left:86px;top:40px;color:var(--ink)">Benefits</h2>

  <div class="benefit" style="left:79px">
    <div class="photo" role="img" aria-label="Photo of a piggy bank with coins" style="background:linear-gradient(135deg,#c9dbe6,#8fb3c9)"></div>
    <h3>Cost Effective</h3>
    <p>KSR allows you to track the cost and effectiveness of your Graffiti Removal. Compare the estimates....</p>
  </div>

  <div class="benefit" style="left:346px">
    <div class="photo" role="img" aria-label="Photo of a wall of street art" style="background:linear-gradient(135deg,#6e6a66,#3a3836)"></div>
    <h3>Photographic Records</h3>
    <p>Store any photographic records of New, Existing and Completed Graffiti Jobs. Archive all competed....</p>
  </div>

  <div class="benefit" style="left:611px">
    <div class="photo" role="img" aria-label="Photo of a judge's gavel on a desk" style="background:linear-gradient(135deg,#b58a5a,#5e3d22)"></div>
    <h3>Assist Prosecution</h3>
    <p>KSR can assist with the possible prosecution of offenders with records of previous tags inside....</p>
  </div>

  <div class="benefit" style="left:876px">
    <div class="photo" role="img" aria-label="Photo of a hand touching a digital security keypad over a world map" style="background:linear-gradient(135deg,#3f8fd6,#0d3f84)"></div>
    <h3>Access and Security</h3>
    <p>You can access your data from any PC around the world connected to the Internet. You can give....</p>
  </div>

  <div class="more-row" style="top:420px"><a class="btn" href="#">More</a></div>
</section>

<section class="help">
  <h2>Just in case you need any help</h2>
  <div class="contact" style="left:80px">
    <svg width="50" height="42" viewBox="0 0 50 42"><path d="M25 2 L48 22 H41 V40 H30 V28 H20 V40 H9 V22 H2 Z" fill="var(--accent)"/></svg>
    <span>Kellwyn Surface Records<br>PO Box 118, Larkfield, NSW 2999</span>
  </div>
  <div class="contact phone" style="left:512px">
    <svg width="30" height="44" viewBox="0 0 30 44"><path d="M6 2 L13 2 L15 12 L10 15 Q12 26 18 32 L23 28 L29 35 L26 42 Q8 40 2 14 Q2 6 6 2 Z" fill="var(--accent)"/></svg>
    <span>(02) 5550 4821</span>
  </div>
  <div class="contact" style="left:872px">
    <svg width="44" height="32" viewBox="0 0 44 32"><rect x="2" y="2" width="40" height="28" fill="none" stroke="var(--accent)" stroke-width="3"/><path d="M2 2 L22 18 L42 2" fill="none" stroke="var(--accent)" stroke-width="3"/></svg>
    <span>enquiries@kellwyn.example<br>support@kellwyn.example</span>
  </div>
</section>

<footer class="site-footer">
  <div class="footer-brand">Kellwyn Surface Records</div>
  <div class="copyright">copyright 2014 KSR all rights reserved</div>
  <div class="social"><span></span><span></span><span></span><span></span></div>
</footer>

</body>
</html>
```